Exclusive beauty salon needs a price list or services booklet

I need a new very attractive flyer for my beauty salon, containing information on the different services and their prices.
In attachment you can find a pdf of the "old" one, but I'd love to have a beautifully designed new one!
I'd love to have a booklet in format 148 x 148 mm, or in US format, containing 12 or 16 pages, but if you can offer other nice looking designs they are welcome!
The services that need to come in the booklet with their prices can all be found on my website: www.atelierverano.be, starting with
Gelaatsverzorging
Wimperverlenging
Suikerontharing
Wimperlifting
Permanente Make Up
Airbrush Tanning

Target Market(s)

woman from 20 to 89 years old

Industry/Entity Type

Beauty Salon

Font styles to use
Sans Serif

Colors

Designer to choose colors to be used in the design.

Requirements
Must have
• a classy nice look, it must contain details about the services from my beauty salon and their prices, and nice pictures.
• The Names, prices and explanations of the services can easily be found on my website: www.atelierverano.be
Nice to have
• In attachment you can find the "old" price list in pdf, what I need now is a "new booklet" with the new logo and updated services price list.
• I need a very nice and attractive looking booklet, classy chique, Paris chique, looking very expensive.
Should not have
• Not too much colors, not too curly, but still feminine

```html
<!DOCTYPE html>
<html lang="nl">
<head>
<meta charset="utf-8">
<title>Airbrush Tanning – De Voorbereiding</title>
<link rel="stylesheet" href="https://fonts.googleapis.com/css2?family=Source+Sans+3:ital,wght@0,400;1,400&display=swap">
<style>
  :root {
    --frame-grey: #9c9d9f;
    --page-white: #ffffff;
    --accent-teal: #5cbfcb;
    --body-grey: #8b8b8b;
    --skin-light: #e9c3a2;
    --skin-deep: #c98a5c;
  }
  * { margin: 0; padding: 0; box-sizing: border-box; }
  html, body {
    width: 1200px;
    height: 868px;
    overflow: hidden;
    background: var(--frame-grey);
  }
  .booklet-page {
    position: absolute;
    left: 34px;
    top: 34px;
    width: 1133px;
    height: 801px;
    background: var(--page-white);
    font-family: "Source Sans 3", "Myriad Pro", sans-serif;
  }
  .service-photo {
    position: absolute;
    left: 0;
    top: 0;
    width: 546px;
    height: 801px;
    background: linear-gradient(100deg, #f4ece8 0%, var(--skin-light) 30%, var(--skin-deep) 58%, var(--skin-light) 80%, #f2e9e6 100%);
  }
  .service-text {
    position: absolute;
    left: 597px;
    top: 76px;
    width: 508px;
  }
  .section-title {
    font-weight: 400;
    font-size: 27px;
    line-height: 1.1;
    color: var(--accent-teal);
    margin-bottom: 12px;
  }
  .section-title + p { margin-top: 0; }
  .body-copy {
    font-style: italic;
    font-size: 16.4px;
    line-height: 23.6px;
    color: var(--body-grey);
    text-align: justify;
    hyphens: auto;
    margin-bottom: 12px;
  }
  .intro { margin-bottom: 40px; }
</style>
</head>
<body>
  <main class="booklet-page">
    <div class="service-photo" role="img" aria-label="Foto van een gebruinde vrouw in zwarte bikini die haar bikinirand optrekt en de bruine tint toont"></div>

    <section class="service-text">
      <h1 class="section-title">Airbrush Tanning</h1>
      <p class="body-copy intro">Altijd al gedroomd van een natuurlijk mooi én egaal bruin kleurtje? En dit zonder te puffen in de zon of te knoeien met zelfbruiner? Ik stel u graag de spraycabine van Solina Glow voor!</p>

      <h2 class="section-title">De Voorbereiding</h2>
      <p class="body-copy">De dag van de afspraak kan je beter geen vette of oliehoudende producten op het lichaam aanbrengen. Een goede scrubbeurt (op waterbasis, zonder olie !!) zal ervoor zorgen dat de kleur mooi egaal en gelijkmatig verdeeld wordt en belangrijker nog, dat je huid veel langer bruin zal blijven. De loszittende dode huidcellen worden verwijderd bij het scrubben. Degene die nog vast zitten zullen nog veel langer op hun plaats blijven. Opgelet : indien je zelf de scrub uitvoert, zorg ervoor dat je geen stukken vergeet !</p>
      <p class="body-copy">Trek donkere loszittende kledij aan. Op lichte kledij kan de gekleurde component licht kleur afgeven. Dit laat zich volledig verwijderen in de was. De kledij mag niet spannen en vooral geen wrijving op de huid geven. De component die de uiteindelijke kleur moet geven werkt gedurende ongeveer 12 uur verder. Op plaatsen waar de kledij op de huid schuurt kan het product vroegtijdig weggewreven worden en dus lichtere strepen geven.</p>
      <p class="body-copy">Het product laat geen vlekken na op de kledij. Alleen op de materialen van zeer fijne lingerie kan het het eventueel inwerken.</p>
    </section>
  </main>
</body>
</html>
```